Design a business card
Business name: Harbourline Growth Advisory
Improving Business Profitibility

- An Overview of the Business & Service:

Business Performance Consulting

- The Target Market: Small to medium-sized business

- Design Specifics:
White card, blue ink, moon eclipse

No Logo

Target Market(s)

Small to medium-sized business

Font styles to use
Sans Serif

```html
<!DOCTYPE html>
<html lang="en">
<head>
<meta charset="UTF-8">
<title>Harbourline Growth Advisory – Business Card</title>
<link href="https://fonts.googleapis.com/css2?family=Oswald:wght@400;500&family=Open+Sans:wght@400&display=swap" rel="stylesheet">
<style>
  :root {
    --ink-blue: #0b428c;
    --card-white: #ffffff;
    --text-dark: #2a2a2a;
    --divider: #d6d6d6;
    --backdrop: #7b7b7b;
  }
  * { margin: 0; padding: 0; box-sizing: border-box; }
  html, body { width: 1200px; height: 802px; overflow: hidden; }
  body { background: var(--backdrop); position: relative; font-family: "Open Sans", sans-serif; }

  .card {
    position: absolute;
    top: 274px;
    width: 443px;
    height: 264px;
    box-shadow: 0 3px 6px rgba(0,0,0,0.35);
  }
  .card-front { left: 136px; background: var(--card-white); }
  .card-back  { left: 624px; background: var(--ink-blue); }

  /* Front: brand block */
  .brand {
    position: absolute;
    left: 0; top: 72px;
    width: 240px;
    text-align: center;
    color: var(--ink-blue);
    font-family: "Oswald", sans-serif;
    font-weight: 500;
  }
  .brand-mark {
    width: 62px; height: 62px;
    border-radius: 50%;
    background: var(--ink-blue);
    margin: 0 auto 14px;
  }
  .brand-name { font-size: 21px; line-height: 1.05; letter-spacing: 0.2px; }
  .brand-sub  { font-size: 12px; letter-spacing: 4.5px; line-height: 1.3; }

  .divider {
    position: absolute;
    left: 240px; top: 34px;
    width: 1px; height: 196px;
    background: var(--divider);
  }

  /* Front: contact block */
  .contact { position: absolute; left: 260px; top: 60px; color: var(--text-dark); }
  .person-name {
    font-family: "Oswald", sans-serif;
    font-weight: 400;
    color: var(--ink-blue);
    font-size: 18px;
    line-height: 1.1;
    text-transform: uppercase;
  }
  .person-role { font-size: 12px; line-height: 1.3; margin-bottom: 7px; }
  .contact-list { list-style: none; }
  .contact-list li {
    display: flex; align-items: center;
    font-size: 12px; line-height: 15.7px;
  }
  .contact-list svg { width: 9px; height: 9px; margin-right: 6px; fill: var(--ink-blue); flex: none; }
  .address { font-size: 12px; line-height: 15.7px; margin-top: 6px; }

  /* Back */
  .back-mark {
    position: absolute;
    left: 50%; top: 46px;
    width: 78px; height: 78px;
    margin-left: -39px;
    border-radius: 50%;
    background: var(--card-white);
  }
  .back-name, .tagline {
    position: absolute; left: 0; width: 100%;
    text-align: center;
    color: var(--card-white);
    font-family: "Oswald", sans-serif;
    font-weight: 400;
    text-transform: uppercase;
  }
  .back-name { top: 138px; font-size: 20px; letter-spacing: 0.4px; }
  .tagline { top: 204px; font-size: 15px; letter-spacing: 0.3px; }
</style>
</head>
<body>
  <section class="card card-front">
    <div class="brand">
      <div class="brand-mark"></div>
      <div class="brand-name">HARBOURLINE GROWTH</div>
      <div class="brand-sub">ADVISORY</div>
    </div>

    <div class="divider"></div>

    <div class="contact">
      <div class="person-name">Desmond R Akerly</div>
      <div class="person-role">Managing Director</div>
      <ul class="contact-list">
        <li>
          <svg viewBox="0 0 10 10" aria-hidden="true"><path d="M1 3.5C1 2 2.5 1 5 1s4 1 4 2.5L7.5 4 7 3H3L2.5 4zM2.5 5h5L9 9H1z"/></svg>
          041-555 0192
        </li>
        <li>
          <svg viewBox="0 0 10 10" aria-hidden="true"><path d="M3 0h4a1 1 0 0 1 1 1v8a1 1 0 0 1-1 1H3a1 1 0 0 1-1-1V1a1 1 0 0 1 1-1zm0 1.3v6.4h4V1.3z"/></svg>
          047-555 0186
        </li>
        <li>
          <svg viewBox="0 0 10 10" aria-hidden="true"><path d="M0.5 2h9v6h-9zM1.5 3v.4L5 5.8l3.5-2.4V3L5 5.3z"/></svg>
          hello@harbourline.co
        </li>
        <li>
          <svg viewBox="0 0 10 10" aria-hidden="true"><circle cx="5" cy="5" r="4.5"/></svg>
          www.harbourline.co
        </li>
      </ul>
      <div class="address">48 Quayside Lane, Suite 12<br>Portmere, 20418</div>
    </div>
  </section>

  <section class="card card-back">
    <div class="back-mark"></div>
    <div class="back-name">Harbourline Growth Advisory</div>
    <div class="tagline">Improving Business Profitibility</div>
  </section>
</body>
</html>
```